FinTech company looking to revamp and expand client-facing interface for our financial models

Pellworth Engines currently has a very simple website that allows clients to interact with our financial models. We are looking to completely redesign the current site and add several extra pages to provide extra functionality. We want the design to have a modern, slick feel, that will work on both a desktop or a tablet. It should be straightforward for clients to move between different pages at any time, and clear from the layout how to interact with the more advanced features. We have included screenshots of existing pages in the attached design brief, as well as sketches of the functionality required by the new pages, but can't provide a direct link to the current site.
Target Market(s)
Professional investors that will be paying to access the interface
Industry/Entity Type
Finance
Number of Pages Required
4 page
Colors
Designer to choose colors to be used in the design.
Look and feel
Each slider illustrates characteristics of the customer's brand and the style your logo design should communicate.

```html
<!DOCTYPE html>
<html lang="en">
<head>
<meta charset="utf-8">
<title>Korvex – Sensitivities</title>
<link rel="stylesheet" href="https://fonts.googleapis.com/css2?family=Open+Sans:wght@600;700&family=Roboto+Condensed:wght@400&display=swap">
<style>
:root{
  --navy:#06345f;
  --ink:#1a1a1a;
  --teal:#006b66;
  --frame:#e4e4e4;
  --white:#ffffff;
  --row-alt:#efefef;
  --line:#e3e3e3;
  --tab-text:#4a4a4a;
}
*{box-sizing:border-box;margin:0;padding:0}
html,body{width:1200px;height:706px;overflow:hidden;background:var(--frame)}
body{font-family:"Open Sans",Arial,sans-serif;color:var(--ink);position:relative}
.app{position:absolute;left:14px;top:14px;width:1172px;height:678px;background:var(--white);overflow:hidden}
.topbar{position:absolute;left:0;top:0;width:100%;height:55px;background:var(--white);box-shadow:0 6px 10px rgba(0,0,0,.08);display:flex;z-index:2}
.brand{width:166px;display:flex;align-items:center;padding-left:53px;font-weight:700;font-size:16px}
.range{width:83px;display:flex;align-items:center;justify-content:center;font-weight:700;font-size:13px;border-right:1px solid var(--line)}
.range.active{background:var(--navy);color:var(--white)}
.spacer{flex:1;border-right:1px solid var(--line)}
.nav-item{display:flex;align-items:center;justify-content:center;gap:8px;font-weight:700;font-size:12px;border-right:1px solid var(--line)}
.nav-item svg{width:20px;height:20px}
.nav-item.models{width:129px}
.nav-item.sens{width:164px;background:var(--navy);color:var(--white)}
.nav-item.favs{width:182px;border:none}
.stage{position:absolute;left:0;top:55px;width:100%;height:623px;background:linear-gradient(#f0f0f0,#f6f6f6)}
.tabs{position:absolute;left:0;top:0;width:100%;height:103px}
.tab{position:absolute;bottom:0;width:143px;background:var(--white);border-radius:4px 4px 0 0;display:flex;align-items:center;justify-content:center;font-weight:700;font-size:12.5px;color:var(--tab-text);box-shadow:0 -2px 6px rgba(0,0,0,.05)}
.tab.short{height:32px}
.tab.mid{height:42px;padding-bottom:8px}
.tab.active{height:51px;background:var(--ink);color:var(--white);padding-bottom:12px}
.tab.arrow{width:37px;height:32px}
.tab.add{width:37px;height:32px;background:var(--navy)}
.content{position:absolute;left:0;top:103px;width:100%;height:520px;background:linear-gradient(#e3e3e3,#ffffff 80%)}
.export{position:absolute;left:1061px;top:38px;display:flex;align-items:center;gap:7px;font-weight:700;font-size:16px;color:var(--navy)}
.filters{position:absolute;left:0;top:151px;width:46px;height:231px;background:var(--ink);border-radius:0 4px 4px 0}
.filters span{position:absolute;left:50%;top:50%;transform:translate(-50%,-50%) rotate(-90deg);color:var(--white);font-weight:700;font-size:14px;letter-spacing:.5px}
.filters-toggle{position:absolute;left:34px;top:105px;width:24px;height:24px}
table.grid{position:absolute;left:83px;top:73px;width:1071px;border-collapse:separate;border-spacing:0;border-radius:7px;overflow:hidden;box-shadow:0 2px 8px rgba(0,0,0,.12);table-layout:fixed}
.grid th{height:65px;font-weight:700;font-size:15px;color:var(--white);background:var(--ink);border-right:1px solid #444}
.grid th.stat{background:var(--teal);border-right:1px solid #0c827c}
.grid th:last-child{border-right:none}
.grid td{height:64px;text-align:center;font-family:"Roboto Condensed","Arial Narrow",sans-serif;font-size:15.5px;background:var(--white);border-right:1px solid var(--line)}
.grid td:last-child{border-right:none}
.grid tr:nth-child(even) td{background:var(--row-alt)}
.col-factor{width:138px}.col-id{width:92px}.col-sector{width:175px}
</style>
</head>
<body>
<div class="app">
  <header class="topbar">
    <div class="brand">KORVEX</div>
    <div class="range active">250D</div>
    <div class="range">83D</div>
    <div class="range">42D</div>
    <div class="spacer"></div>
    <div class="nav-item models">
      <svg viewBox="0 0 24 24"><path d="M3 11 12 3l9 8M6 9v11h4v-6h4v6h4V9" fill="none" stroke="#1a1a1a" stroke-width="2.2" stroke-linejoin="round"/></svg>MODELS</div>
    <div class="nav-item sens">
      <svg viewBox="0 0 24 24" fill="#fff"><circle cx="12" cy="12" r="2"/><circle cx="12" cy="5" r="1.5"/><circle cx="12" cy="19" r="1.5"/><circle cx="5" cy="12" r="1.5"/><circle cx="19" cy="12" r="1.5"/><circle cx="7" cy="7" r="1.3"/><circle cx="17" cy="7" r="1.3"/><circle cx="7" cy="17" r="1.3"/><circle cx="17" cy="17" r="1.3"/><circle cx="12" cy="1.5" r=".9"/><circle cx="12" cy="22.5" r=".9"/><circle cx="1.5" cy="12" r=".9"/><circle cx="22.5" cy="12" r=".9"/></svg>SENSITIVITIES</div>
    <div class="nav-item favs">
      <svg viewBox="0 0 24 24"><path d="M12 2.5l2.9 6.2 6.6.7-5 4.5 1.4 6.6L12 17.2l-5.9 3.3 1.4-6.6-5-4.5 6.6-.7z" fill="none" stroke="#1a1a1a" stroke-width="1.8" stroke-linejoin="round"/></svg>FAVOURITES</div>
  </header>

  <main class="stage">
    <nav class="tabs">
      <div class="tab short" style="left:51px">EQUITIES</div>
      <div class="tab short" style="left:198px">ETFS</div>
      <div class="tab mid" style="left:346px">PAIRS</div>
      <div class="tab active" style="left:494px">ETF PAIRS</div>
      <div class="tab mid" style="left:641px">FACTORS</div>
      <div class="tab short" style="left:789px">NEW TAB TITLE #1</div>
      <div class="tab short" style="left:937px">NEW TAB TITLE #2</div>
      <div class="tab arrow" style="left:1085px"><svg width="12" height="16" viewBox="0 0 12 16"><path d="M3 2l6 6-6 6" fill="none" stroke="#777" stroke-width="2.5"/></svg></div>
      <div class="tab add" style="left:1126px"><svg width="22" height="22" viewBox="0 0 22 22"><circle cx="11" cy="11" r="9" fill="none" stroke="#fff" stroke-width="1.8"/><path d="M11 6v10M6 11h10" stroke="#fff" stroke-width="1.8"/></svg></div>
    </nav>

    <section class="content">
      <div class="export"><svg width="24" height="22" viewBox="0 0 24 22"><path d="M10 4H3v16h16v-6" fill="none" stroke="#06345f" stroke-width="2.2"/><path d="M8 14c2-6 6-8 12-8M16 2l5 4-5 4" fill="none" stroke="#06345f" stroke-width="2.2"/></svg>Export</div>

      <div class="filters"><span>FILTERS</span>
        <svg class="filters-toggle" viewBox="0 0 24 24"><circle cx="12" cy="12" r="11" fill="#fff"/><circle cx="12" cy="12" r="9" fill="#06345f"/><path d="M7 12h9M12.5 8l4 4-4 4" fill="none" stroke="#fff" stroke-width="2"/></svg>
      </div>

      <table class="grid">
        <thead><tr>
          <th class="col-factor">Factor</th><th class="col-id">ID ⌄</th><th class="col-sector">Sector</th>
          <th class="stat">Stat 1</th><th class="stat">Stat 2</th><th class="stat">Stat 3</th><th class="stat">Stat 4</th><th class="stat">Stat 5</th><th class="stat">Stat 6</th><th class="stat">Stat 7</th><th class="stat">Stat 8</th>
        </tr></thead>
        <tbody>
          <tr><td>Factor 1</td><td>Model 1</td><td>Materials</td><td>-1.4</td><td>0.1</td><td>-3.1</td><td>0.7</td><td>30.2</td><td>0.9</td><td>-3.1</td><td>0.1</td></tr>
          <tr><td>Factor 2</td><td>Model 2</td><td>Materials</td><td>2.8</td><td>0.1</td><td>6.1</td><td>100</td><td>30.2</td><td>0.9</td><td>6.1</td><td>0.1</td></tr>
          <tr><td>Factor 3</td><td>Model 3</td><td>Materials</td><td>-3.7</td><td>2.7</td><td>-7.2</td><td>100</td><td>30.2</td><td>0.9</td><td>-7.2</td><td>2.7</td></tr>
          <tr><td>Factor 4</td><td>Model 4</td><td>Industrials</td><td>2.8</td><td>0.2</td><td>2.7</td><td>0.5</td><td>32.9</td><td>-0.5</td><td>2.7</td><td>0.2</td></tr>
          <tr><td>Factor 5</td><td>Model 5</td><td>Industrials</td><td>0.8</td><td>0.3</td><td>2.5</td><td>0.5</td><td>32.9</td><td>-0.5</td><td>2.5</td><td>0.3</td></tr>
        </tbody>
      </table>
    </section>
  </main>
</div>
</body>
</html>
```